Hollow Thicket, a 3d voxel survival video game needs a card for gaming conventions

I am the lead developer for Hollow Thicket http://www.HollowThicket.example and need a business card to hand out at an indie gaming convention
The card would need to include the game name, website url, my name, position (Lead Developer), e-mail and phone number
The game is a 3d, voxel (with smooth terrain) based survival game with guns and wildlife. The main icon of the game would likely be a grizzly bear but I am willing to accept other designs too.
Attached is a media kit for the game with some images you can use but don't have to its just what little art I can provide. Anything on the website or from the video game can also be used. unrelated art can also be used.
Target Market(s)
Indie Developers/publishers at conferences
Industry/Entity Type
Games
Contact Information for Business Card
Name: Corin Waldrick
Position: Lead Developer
E-mail: Pale_Kettle@mailbox.example
Phone number: 555-372-1186

```html
<!DOCTYPE html>
<html lang="en">
<head>
<meta charset="utf-8">
<title>Hollow Thicket — Business Card</title>
<link href="https://fonts.googleapis.com/css2?family=Open+Sans:wght@400;600;800&display=swap" rel="stylesheet">
<style>
  :root {
    --page: #ece9e2;
    --ink: #1d1d1b;
    --ink-soft: #3a3a36;
    --brand-red: #b8352a;
    --sky-top: #c9d4e4;
    --sky-low: #dfe6ee;
    --foliage: #8fa57a;
    --bear-light: #a88260;
    --bear: #7a5638;
    --back-edge: #1f1f12;
    --back-mid: #4c4a2c;
    --back-glow: #e4e2cf;
    --chip: #8c929b;
  }
  * { box-sizing: border-box; margin: 0; padding: 0; }
  html, body { width: 1200px; height: 780px; overflow: hidden; }
  body {
    background: var(--page);
    font-family: "Open Sans", sans-serif;
    position: relative;
  }
  .card {
    position: absolute;
    top: 240px;
    width: 520px;
    height: 300px;
    overflow: hidden;
    border-radius: 4px;
    box-shadow: 0 8px 24px rgba(0,0,0,.18);
  }
  .card--front { left: 50px; }
  .card--back { left: 630px; }

  /* Front */
  .scene-art {
    position: absolute; inset: 0;
    background:
      radial-gradient(ellipse 45% 40% at 30% 55%, rgba(143,165,122,.5), transparent 70%),
      linear-gradient(180deg, var(--sky-top), var(--sky-low));
  }
  .bear-art {
    position: absolute;
    left: 250px; top: 12px;
    width: 260px; height: 122px;
    background: radial-gradient(ellipse 55% 55% at 50% 50%, var(--bear-light), var(--bear) 45%, rgba(122,86,56,0) 100%);
  }
  .social {
    position: absolute; left: 34px; bottom: 104px;
    display: flex; gap: 8px;
  }
  .social span {
    width: 20px; height: 20px; border-radius: 3px;
    background: var(--chip);
  }
  .details {
    position: absolute; left: 170px; bottom: 22px;
    color: var(--ink);
  }
  .brand-name {
    font-weight: 800;
    font-size: 20px;
    letter-spacing: 1px;
    text-transform: uppercase;
    color: var(--brand-red);
    margin-bottom: 6px;
    line-height: 1.1;
  }
  .person-name { font-size: 19px; font-weight: 600; line-height: 1.1; }
  .person-role { font-size: 13px; color: var(--ink-soft); margin-bottom: 8px; }
  .contact-list { list-style: none; font-size: 13px; line-height: 1.5; }
  .contact-list li { display: flex; align-items: center; gap: 8px; }
  .contact-list svg { width: 12px; height: 12px; flex: none; }

  /* Back */
  .card--back {
    background: radial-gradient(ellipse 55% 60% at 50% 50%, var(--back-glow), var(--back-mid) 65%, var(--back-edge) 100%);
  }
  .bear-head-art {
    position: absolute;
    left: 320px; top: 50px;
    width: 150px; height: 90px;
    background: radial-gradient(ellipse 55% 55% at 50% 50%, #8d6240, rgba(110,74,46,0) 100%);
  }
  .back-mark {
    position: absolute; left: 70px; top: 70px;
  }
  .back-mark .brand-name {
    font-size: 46px;
    letter-spacing: 3px;
    line-height: 1.05;
    margin-bottom: 10px;
  }
  .back-url {
    font-size: 16px; font-weight: 800;
    color: var(--brand-red);
  }
</style>
</head>
<body>

<section class="card card--front">
  <div class="scene-art" role="img" aria-label="Soft photo of a rocky wilderness with trees under a pale sky"></div>
  <div class="bear-art" role="img" aria-label="Photo of a grizzly bear standing on a ridge"></div>

  <div class="social" aria-label="Social profiles">
    <span></span><span></span><span></span>
  </div>

  <div class="details">
    <p class="brand-name">Hollow Thicket</p>
    <p class="person-name">Corin Waldrick</p>
    <p class="person-role">Lead Developer</p>
    <ul class="contact-list">
      <li>
        <svg viewBox="0 0 12 12"><path d="M2 1h3l1 3-1.5 1a6 6 0 0 0 2.5 2.5L8 6l3 1v3a1 1 0 0 1-1 1A9 9 0 0 1 1 2a1 1 0 0 1 1-1z" fill="var(--ink)"/></svg>
        555-372-1186
      </li>
      <li>
        <svg viewBox="0 0 12 12"><rect x="0.5" y="2" width="11" height="8" fill="var(--ink)"/><path d="M0.5 2l5.5 4.5L11.5 2" stroke="#fff" fill="none"/></svg>
        Pale_Kettle@mailbox.example
      </li>
      <li>
        <svg viewBox="0 0 12 12" fill="none" stroke="var(--ink)"><circle cx="6" cy="6" r="5"/><ellipse cx="6" cy="6" rx="2.2" ry="5"/><path d="M1 6h10"/></svg>
        www.HollowThicket.example
      </li>
    </ul>
  </div>
</section>

<section class="card card--back">
  <div class="bear-head-art" role="img" aria-label="Photo of a roaring grizzly bear head"></div>
  <div class="back-mark">
    <p class="brand-name">Hollow<br>Thicket</p>
    <p class="back-url">www.HollowThicket.example</p>
  </div>
</section>

</body>
</html>
```